Corvane Capital Business Cards

These are professional business cards that are for my family office.
Put fake emails and phone numbers as of now until I finalize those components. This family office controls my families investments, assets, and future. The cards should be professional.
..
.
.
.
I just uploaded another variation of a logo I would like to see as a business card to I am inbeteen which logo to use

Target Market(s)

business

Industry/Entity Type

business

Contact Information for Business Card

Professional, wealth related, finance related.

Requirements
Must have
• Logo

```html
<!DOCTYPE html>
<html lang="en">
<head>
<meta charset="utf-8">
<title>Corvane Capital Business Cards</title>
<link href="https://fonts.googleapis.com/css2?family=Cinzel:wght@600&family=Inter:wght@500;600&display=swap" rel="stylesheet">
<style>
  :root {
    --page-bg: #e0e0e0;
    --card-dark: #1f1f1f;
    --card-light: #fafbfb;
    --ink-navy: #151c2a;
    --ink-grey: #8a8a8a;
    --ink-contact: #555a60;
    --white: #ffffff;
  }
  * { margin: 0; padding: 0; box-sizing: border-box; }
  html, body {
    width: 1200px; height: 1200px; overflow: hidden;
    background: var(--page-bg);
  }
  .sheet { position: relative; width: 1200px; height: 1200px; }
  .card {
    position: absolute; left: 179px; width: 861px; height: 496px;
    overflow: hidden;
  }
  .card-front {
    top: 84px; background: var(--card-dark);
    display: flex; align-items: center; justify-content: center;
  }
  .card-back { top: 622px; background: var(--card-light); }

  .front-name {
    font-family: "Cinzel", serif; font-weight: 600; font-size: 40px;
    color: var(--white); letter-spacing: 1px;
  }

  .back-name {
    position: absolute; left: 27px; top: 58px;
    font-family: "Cinzel", serif; font-weight: 600; font-size: 38px;
    color: var(--ink-navy); letter-spacing: 0.5px; line-height: 1;
  }
  .accent-bar {
    position: absolute; left: 0; top: 213px; width: 14px; height: 55px;
    background: var(--ink-navy);
  }
  .person { position: absolute; left: 31px; top: 204px; font-family: "Inter", sans-serif; }
  .person-name {
    font-size: 36px; font-weight: 600; color: var(--ink-navy);
    letter-spacing: 2.2px; line-height: 40px;
  }
  .person-role {
    font-size: 28px; font-weight: 600; color: var(--ink-grey);
    letter-spacing: 0.5px; line-height: 32px; margin-top: -2px;
  }

  .contact-list { position: absolute; left: 30px; top: 366px; list-style: none; font-family: "Inter", sans-serif; }
  .contact-item {
    display: flex; align-items: center; height: 34px;
    font-size: 26px; font-weight: 500; color: var(--ink-contact); letter-spacing: 4px;
  }
  .contact-icon { width: 24px; height: 24px; margin-right: 14px; flex: none; }
</style>
</head>
<body>
<main class="sheet">
  <section class="card card-front" aria-label="Card front">
    <span class="front-name">Corvane Capital</span>
  </section>

  <section class="card card-back" aria-label="Card back">
    <div class="back-name">Corvane Capital</div>

    <div class="accent-bar"></div>
    <div class="person">
      <div class="person-name">ELLIOT MARSH</div>
      <div class="person-role">Founder</div>
    </div>

    <ul class="contact-list">
      <li class="contact-item">
        <svg class="contact-icon" viewBox="0 0 24 24" aria-hidden="true">
          <path d="M6.6 3.5l2.6 3.6-1.7 2.2c1 2.3 2.9 4.2 5.2 5.2l2.2-1.7 3.6 2.6-1.4 3.6c-7.4-.2-13.6-6.4-13.8-13.8z" fill="none" stroke="var(--ink-navy)" stroke-width="2" stroke-linejoin="round"/>
          <path d="M14 3.5a6.5 6.5 0 0 1 6.5 6.5M14 7a3 3 0 0 1 3 3" fill="none" stroke="var(--ink-navy)" stroke-width="1.8" stroke-linecap="round"/>
        </svg>
        <span>800-222-2222</span>
      </li>
      <li class="contact-item">
        <svg class="contact-icon" viewBox="0 0 24 24" aria-hidden="true">
          <rect x="2" y="6" width="20" height="13" fill="var(--ink-navy)"/>
          <path d="M2.5 6.5l9.5 7 9.5-7" fill="none" stroke="var(--card-light)" stroke-width="1.6"/>
        </svg>
        <span>email@yoursite.com</span>
      </li>
      <li class="contact-item">
        <svg class="contact-icon" viewBox="0 0 24 24" aria-hidden="true">
          <g fill="none" stroke="var(--ink-navy)" stroke-width="1.8">
            <circle cx="12" cy="12" r="9.5"/>
            <ellipse cx="12" cy="12" rx="4.2" ry="9.5"/>
            <path d="M2.5 12h19M4 7.5h16M4 16.5h16"/>
          </g>
        </svg>
        <span>www.yoursite.com</span>
      </li>
    </ul>
  </section>
</main>
</body>
</html>
```